The Brandwell Firm

We need a new design for our letterhead and envelopes. We are a personal injury and criminal defense firm so we need something modern and clean, but more on the professional/traditional side. Our new logo has two colors and is attached to the file so we need something that works well with those colors/matches the design. The following information needs to be on the letterhead:
Phone: (555) 214-3370
Fax: (555) 214-5186
Toll-Free: (888) 431-2059
Post Office Box 4721
Millbrook, SC 29555-4721
HarmClaimCounsel.example
PalmettoTrialAdvocates.example

Target Market(s)

Clients, government agencies, other law firms

Industry/Entity Type

Legal

Font styles to use
Sans Serif
Other font styles liked:
• Arial

Colors

Designer to choose colors to be used in the design.

Requirements
Must have
• Must look professional and clean, modern
Nice to have
• I would like to see a design that works with the logo but does not distract from the content that will be printed on it
Should not have
• Too many colors or crazy designs.

```html
<!DOCTYPE html>
<html lang="en">
<head>
<meta charset="utf-8">
<title>The Brandwell Firm — Letterhead and Envelopes</title>
<link href="https://fonts.googleapis.com/css2?family=Roboto:wght@400;500&family=Lato:wght@700&display=swap" rel="stylesheet">
<style>
  :root {
    --bg: #c3c3c3;
    --paper: #ffffff;
    --brand-blue: #3a3b98;
    --flap-blue: #46449b;
    --brand-red: #d1202a;
    --ink: #555555;
    --ink-dark: #3c3c3c;
  }
  * { margin: 0; padding: 0; box-sizing: border-box; }
  html, body { width: 1200px; height: 810px; overflow: hidden; }
  body {
    position: relative;
    background: var(--bg);
    font-family: "Roboto", Arial, sans-serif;
    color: var(--ink);
  }

  .brand-name {
    display: flex; align-items: center; gap: 7px;
    font-family: "Roboto", Arial, sans-serif;
    font-weight: 500; color: var(--brand-blue);
    white-space: nowrap;
  }
  .brand-dot { width: 14px; height: 14px; border-radius: 50%; background: var(--brand-red); flex: none; }

  /* Letterhead */
  .letterhead {
    position: absolute; left: 137px; top: 110px;
    width: 436px; height: 614px; background: var(--paper);
  }
  .letterhead .brand-name { position: absolute; left: 38px; top: 60px; font-size: 19px; }
  .contact-block {
    position: absolute; left: 308px; top: 54px;
    font-size: 7.4px; line-height: 9px; color: var(--ink-dark);
  }
  .contact-numbers { margin-top: 6px; display: grid; grid-template-columns: 32px 8px auto; }
  .contact-numbers dt { font-family: "Lato", Arial, sans-serif; font-weight: 700; color: var(--brand-blue); }
  .recipient {
    position: absolute; left: 38px; top: 200px;
    font-size: 7.6px; line-height: 11.4px;
  }
  .letter-body {
    position: absolute; left: 38px; top: 268px; width: 362px;
    font-size: 7.6px; line-height: 11.4px; text-align: justify;
  }
  .letter-body p + p { margin-top: 22px; }
  .signature {
    position: absolute; left: 38px; top: 436px; width: 82px; height: 52px;
    background: linear-gradient(135deg, #e9e9f4, #d7d8ec); border-radius: 3px;
  }
  .signer-title { position: absolute; left: 37px; top: 502px; font-size: 7.6px; }

  .web-footer {
    position: absolute; left: 0; right: 0; bottom: 18px;
    display: flex; align-items: center; gap: 6px;
    font-size: 7.8px; color: var(--ink-dark); white-space: nowrap;
  }
  .web-footer .rule { flex: 1; height: 3px; background: var(--brand-red); }
  .web-footer .sep { width: 1.5px; height: 6px; background: var(--ink-dark); margin: 0 3px; }
  .blue-band { position: absolute; left: 0; right: 0; bottom: 0; background: var(--brand-blue); }
  .letterhead .blue-band { height: 18px; }

  /* Envelope back */
  .envelope-back {
    position: absolute; left: 605px; top: 194px;
    width: 444px; height: 220px; background: var(--paper);
  }
  .envelope-flap { position: absolute; left: 0; top: 0; width: 444px; height: 66px; }

  /* Envelope front */
  .envelope-front {
    position: absolute; left: 604px; top: 444px;
    width: 445px; height: 220px; background: var(--paper);
  }
  .envelope-front .brand-name { position: absolute; left: 19px; top: 40px; font-size: 17px; }
  .return-address {
    position: absolute; left: 19px; top: 93px;
    font-size: 7.2px; line-height: 9px; color: var(--ink-dark);
  }
  .envelope-front .web-footer { bottom: 19px; }
  .envelope-front .blue-band { height: 16px; }
</style>
</head>
<body>

<section class="letterhead">
  <div class="brand-name"><span class="brand-dot"></span>The Brandwell Firm</div>

  <address class="contact-block">
    <div>Post Office Box 4721</div>
    <div>Millbrook, SC 29555-4721</div>
    <dl class="contact-numbers">
      <dt>Phone</dt><dd>:</dd><dd>(555) 214-3370</dd>
      <dt>Fax</dt><dd>:</dd><dd>(555) 214-5186</dd>
      <dt>Toll-Free</dt><dd>:</dd><dd>(888) 431-2059</dd>
    </dl>
  </address>

  <div class="recipient">
    <div>Dear Halvorsen</div>
    <div>Ridgeline Print Group Corporation</div>
    <div>Department Design</div>
  </div>

  <div class="letter-body">
    <p>Lorem ipsum dolor sit amet, consectetuer adipiscing elit. Aenean commodo ligula eget dolor. Aenean massa. Cum sociis natoque penatibus et magnis dis parturient montes, nascetur ridiculus mus. Donec quam felis, ultricies nec, pellentesque eu, pretium quis, sem. Nulla consequat massa quis enim. Donec pede justo, fringilla vel, aliquet nec, vulputate eget, arcu. In enim justo, rhoncus ut, imperdiet a, venenatis vitae, justo. Nullam dictum felis eu pede mollis pretium. Integer tincidunt. Cras dapibus. Vivamus elementum semper nisi.Nullam dictum felis eu pede mollis pretium. Integer tincidunt. Cras dapibus. Vivamus elementum semper nisi.felis eu pede mollis pretium. Integer tincidunt. Cras dapibus.</p>
    <p>Quisque rutrum. Aenean imperdiet. Etiam ultricies nisi vel augue. Curabitur ullamcorper ultricies nisi. Nam eget dui. Etiam rhoncus. Maecenas tempus, tellus eget condimentum rhoncus, sem quam semper libero, sit amet adipiscing sem neque sed ipsum.felis pede mollis pretium. I am tincidunt. Cras dapibus.</p>
  </div>

  <div class="signature" role="img" aria-label="Handwritten signature of the director"></div>
  <div class="signer-title">Director/Excecutive Director</div>

  <div class="web-footer">
    <span class="rule"></span>
    <span>www.HarmClaimCounsel.example</span><span class="sep"></span><span>www.PalmettoTrialAdvocates.example</span>
    <span class="rule"></span>
  </div>
  <div class="blue-band"></div>
</section>

<section class="envelope-back">
  <svg class="envelope-flap" viewBox="0 0 444 66" aria-hidden="true">
    <path d="M0 0 H444 V4 L436 56 Q434 66 424 66 H20 Q10 66 8 56 L0 4 Z" fill="var(--flap-blue)"/>
  </svg>
</section>

<section class="envelope-front">
  <div class="brand-name"><span class="brand-dot"></span>The Brandwell Firm</div>
  <address class="return-address">
    <div>Post Office Box 4721</div>
    <div>Millbrook, SC 29555-4721</div>
  </address>
  <div class="web-footer">
    <span class="rule"></span>
    <span>www.HarmClaimCounsel.example</span><span class="sep"></span><span>www.PalmettoTrialAdvocates.example</span>
    <span class="rule"></span>
  </div>
  <div class="blue-band"></div>
</section>

</body>
</html>
```